Market place for used airplanes/helicopters/parts

http://www.vingtorget.se needs a facelift.

# What is it
Classifieds for used airplanes/helicopters/parts/spare parts/aviation literature, for people in Scandinavia. The number of classifieds is ~120-200. They are mainly in Swedish, English, Norwegian.

It's not a glamorous or luxurious business, but more for people with a genuine interest in flying, technical things.

Similar to sites like this, but they have much more classifieds than my site
http://www.skyvendor.com/list/list.aspx?ETID=1&setype=1&catid=6
http://www.lindqvistflyg.com/planes.asp?meny=1&typ=single
https://www.hangarhub.com/cat.php?mode=listing&main=

# What I want
Design only - no code. I want a modern, maybe a bit bootstrap like, clean, simple, not flashy, web design. I want the design to be in English.

# Audience of the website
Aviation interested men, 45-65 years old, in the nordic countries (around Sweden).

# Logotype that could be used (but not necessarily)
http://www.vingtorget.se/flygplan_till_salu_large.jpg
http://www.vingtorget.se/flygplan_till_salu.eps

Reason: I decided to extend the deadline with 1 day. The reason is that I (unfortunately) managed to put the contest in the wrong category for 1 day + I want to give you all feedback (been too busy the whole day, sorry).

Hi all! 

Thanks everyone for the contributions you made. 

I will setup a poll for the designs that I like most. Will get back when I have more information. 

Thanks and have a nice weekend!
Erik

Target Market(s)

45-65 old Scandinavian men

Industry/Entity Type

Business

Requirements
Must have
• - A list with classifieds on the first page, so the visitor easily can see new classifieds.
- A classifieds should be able to have more than one photo
- A simple navigation for showing classifieds from categories like airplanes, helicopters/gyrocopters, parts, literature, misc (maybe other categories) .... but still, it's just 100-200 ads so it's not needed that much filtration.

- A placeholder/way of showing aviation news/clips. In the old design I had, it was a column to the right. It's enough to show maybe 2-5 placeholders.
- A placeholder for PlaceMint ads somewhere on the site.
Should not have
• - Carousels
- Too much clutter

```html
<!DOCTYPE html>
<html lang="en">
<head>
<meta charset="utf-8">
<title>Vingtorget – Aircraft for Sale</title>
<link href="https://fonts.googleapis.com/css2?family=PT+Sans:wght@400;700&display=swap" rel="stylesheet">
<style>
:root{
  --navy:#0d3f86;
  --nav-top:#1b5db0;
  --nav-bottom:#0b3e85;
  --cyan:#1aa7e6;
  --cyan-dark:#0e8fcc;
  --text:#333;
  --muted:#555;
  --red:#c8101e;
  --link:#1a8ed1;
  --line:#cfcfcf;
  --footer:#111;
}
*{box-sizing:border-box;margin:0;padding:0}
html,body{width:686px;height:1200px;overflow:hidden}
body{position:relative;font-family:"PT Sans",sans-serif;color:var(--text);
  background:linear-gradient(#c6def2 0,#e6f1fa 220px,#fff 420px,#fff 1000px,#e3eef8 1130px);}
.abs{position:absolute}
.brand{left:95px;top:30px;display:flex;align-items:center;gap:8px;font-size:34px;font-weight:700;color:var(--navy);letter-spacing:.5px}
.brand-mark{width:14px;height:14px;background:var(--cyan);border-radius:50%}
.account{top:8px;left:480px;font-size:7.5px;color:#333;display:flex;gap:20px}
.account span::before{content:"";display:inline-block;width:6px;height:7px;background:#222;border-radius:1px;margin-right:5px;vertical-align:-1px}
.search{left:482px;top:54px;width:126px;height:14px;background:#fff;border:1px solid #ddd;border-radius:3px;font-size:6px;color:#999;padding:3px 5px}
.search svg{position:absolute;right:4px;top:3px}
.nav{left:80px;top:93px;width:531px;height:32px;border-radius:3px;background:linear-gradient(var(--nav-top),var(--nav-bottom));display:flex;box-shadow:0 2px 4px rgba(0,0,0,.25)}
.nav a{color:#fff;text-decoration:none;font-size:9.5px;padding:0 16px;line-height:32px;border-right:1px solid rgba(255,255,255,.18)}
.nav a:first-child{padding-left:20px}
.listing-title{left:86px;top:141px;font-size:14px;font-weight:700;color:var(--navy);font-variant:small-caps;letter-spacing:.3px}
.listing-title b{color:var(--cyan-dark)}
.dots{left:86px;width:333px;border-top:2px dotted #cfcfcf}
.photo{background:linear-gradient(135deg,#d9d9d9,#f2f2f2 45%,#8a8f96);border:1px solid #bbb}
.photo.main{left:89px;top:177px;width:181px;height:98px;border:2px solid #3b7cc4}
.thumb{width:57px;height:44px;border:2px solid #bbb}
.thumb.sel{border-color:#3b7cc4}
.details{left:89px;top:286px;width:330px;font-size:7.2px;color:var(--muted);line-height:9.6px}
.details p{margin-bottom:3px}
.details .contact{line-height:12px;margin-top:-1px}
.btn{background:var(--cyan);color:#fff;border-radius:3px;text-align:center;font-weight:700}
.more-main{left:359px;top:386px;width:59px;height:21px;line-height:21px;font-size:10px;font-variant:small-caps}
.cards{left:86px;top:434px;display:grid;grid-template-columns:152px 152px;column-gap:28px;row-gap:0;grid-auto-rows:223px}
.card-img{width:152px;height:94px;border:3px solid #fff;border-radius:4px;box-shadow:0 0 3px rgba(0,0,0,.35)}
.card h3{font-weight:400;font-size:9px;color:#111;margin:13px 0 5px}
.card p{font-size:7.2px;line-height:9.3px;color:#333}
.card .price{color:var(--link)}
.card .email{color:var(--link)}
.card-foot{position:relative}
.card .btn{position:absolute;left:97px;top:-21px;width:49px;height:16px;line-height:16px;font-size:7px;font-weight:400}
.rule{left:86px;top:1092px;width:333px;border-top:1px solid var(--line)}
.pager{top:1106px;width:11px;height:11px;background:var(--cyan);border:1px solid #0a78b2;font-size:7px;color:#0b2c55;text-align:center;line-height:9px}
.panel{background:#fff;border:1px solid #e2e2e2;border-radius:4px;box-shadow:0 6px 6px -4px rgba(0,0,0,.25)}
.panel-head{position:absolute;left:5px;top:5px;right:5px;height:24px;background:var(--cyan);border-radius:3px;color:#fff;font-size:12px;font-weight:400;padding:3px 8px}
.news{left:456px;top:136px;width:154px;height:214px}
.news-item{position:absolute;left:9px;display:flex;gap:7px}
.news-item .pic{width:38px;height:38px;border-radius:2px;box-shadow:0 1px 3px rgba(0,0,0,.4)}
.news-item p{font-size:6.4px;line-height:9px;color:#333;width:94px}
.more{display:block;text-align:right;color:var(--red);font-size:6.4px}
.clips{left:456px;top:373px;width:154px;height:173px}
.clip{position:absolute;left:6px;display:flex;gap:7px}
.clip .pic{width:52px;height:40px;border-radius:2px;box-shadow:0 1px 3px rgba(0,0,0,.4)}
.clip p{font-size:6.4px;line-height:9px;color:#333;width:81px;text-align:justify}
.ads{left:454px;top:566px;width:157px;height:131px;border:1px solid #4b7fc4;background:#fff;padding:5px 2px;font-size:5px;line-height:6.2px;color:#222}
.ads div{margin-bottom:6px}
.ads b{color:#1b3fbf;text-decoration:underline;font-size:5.2px}
.ads i{color:#1c8a2a;font-style:normal;display:block}
.ads-tag{position:absolute;right:0;bottom:0;background:#1b3f8a;color:#fff;font-size:5px;padding:1px 4px}
.banner1{left:454px;top:712px;width:157px;height:155px;background:linear-gradient(160deg,#8c2f8f,#5b1d6e)}
.banner2{left:454px;top:890px;width:156px;height:155px;background:linear-gradient(#1b2a52,#2e4a8a 60%,#e9572b 88%)}
footer{position:absolute;left:0;top:1130px;width:686px;height:70px;background:var(--footer);color:#fff}
.connect{position:absolute;left:92px;top:12px;font-size:11px;color:#eee}
.social{position:absolute;left:90px;top:34px;display:flex;gap:3px}
.social span{width:17px;height:17px;border-radius:50%;background:#eee}
.social span:first-child{background:#3f6fc2}
.legal{position:absolute;right:99px;top:17px;text-align:right;font-size:6.6px;line-height:12px;color:#ddd}
</style>
</head>
<body>
<header>
  <div class="abs brand"><span class="brand-mark"></span>VINGTORGET</div>
  <div class="abs account"><span>Login</span><span>Register</span></div>
  <div class="abs search">Search
    <svg width="8" height="8" viewBox="0 0 8 8"><circle cx="3.2" cy="3.2" r="2.4" fill="none" stroke="#bbb" stroke-width="1"/><path d="M5 5l2.5 2.5" stroke="#bbb" stroke-width="1.2"/></svg>
  </div>
  <nav class="abs nav"><a>Airplanes</a><a>Helicopters</a><a>Parts</a><a>literature</a><a>Misc</a></nav>
</header>

<main>
  <h1 class="abs listing-title">Veltair <b>VX-4 UL</b></h1>
  <div class="abs dots" style="top:162px"></div>
  <div class="abs photo main" role="img" aria-label="White carbon-fibre ultralight aircraft in a hangar"></div>
  <div class="abs photo thumb sel" style="left:282px;top:178px" role="img" aria-label="Aircraft side view"></div>
  <div class="abs photo thumb" style="left:356px;top:178px" role="img" aria-label="Instrument panel"></div>
  <div class="abs photo thumb" style="left:282px;top:233px" role="img" aria-label="Aircraft with owner on airfield"></div>
  <div class="abs photo thumb" style="left:356px;top:233px" role="img" aria-label="Wing detail"></div>

  <div class="abs details">
    <p>A unique UL machine in carbon fiber, it makes it exceptionally easy. Empty weight 268kg</p>
    <p style="margin-top:6px">Manuf. 2006, ca.260 hours, always in hangar.</p>
    <p style="margin-top:6px;line-height:8px">Equipped with constant-speed propeller and save screen. Analog plus EFIS. Holder for Navrex 410 GPS integrated in the panel. Motrax 100HP. Air Worthy to 140512th Cruising 65% FL110 288 km / h Climb rate FL 0 1950ft/min, Fuel consumption 65% 5.18 liter / h See the manufacturer's data on: further information:</p>
    <p class="contact">Email: lars.hedberg @ fjordmail.net<br>Tel. +46-700-11 22 33<br>Name: Lars Hedberg,<br>Email Phone: +46-700-11 22 33<br>Date: 2013-10-04 16 : 49:39</p>
  </div>
  <div class="abs btn more-main">More</div>
  <div class="abs dots" style="top:418px"></div>

  <section class="abs cards">
    <article class="card">
      <div class="card-img photo" role="img" aria-label="Red and white aerobatic aircraft in flight"></div>
      <h3>Aerobatic Ranford R-7 LN-QAB</h3>
      <p>Experimental clipped wing +9 /-6G airshow performer for sale in Norway. Two stroke Bluecrest BT70 fully inverted system.<br>Asking <span class="price">€ 26000</span><br>Name: Arne Solvik, <span class="email">Email</span><br>Phone: +4790001234<br>Date: 2013-10-04 12:23:08</p>
      <div class="card-foot"><div class="btn">More &gt;&gt;</div></div>
    </article>
    <article class="card">
      <div class="card-img photo" role="img" aria-label="Red and white single-engine aircraft on grass"></div>
      <h3>Pelham Chinook 150 Auto STC</h3>
      <p>Experimental clipped wing +9 /-6G airshow performer for sale in Norway. Two stroke Bluecrest BT70 fully inverted system.<br>Asking <span class="price">€ 26000</span><br>Name: Arne Solvik, <span class="email">Email</span><br>Phone: +4790001234<br>Date: 2013-10-04 12:23:08</p>
      <div class="card-foot"><div class="btn">More &gt;&gt;</div></div>
    </article>
    <article class="card">
      <div class="card-img photo" role="img" aria-label="Seaplane on a river under a bridge"></div>
      <h3>N KTV HK180T 1973 Salg wil!</h3>
      <p>Experimental clipped wing +9 /-6G airshow performer for sale in Norway. Two stroke Bluecrest BT70 fully inverted system.<br>Asking <span class="price">€ 26000</span><br>Name: Arne Solvik, <span class="email">Email</span><br>Phone: +4790001234<br>Date: 2013-10-04 12:23:08</p>
      <div class="card-foot"><div class="btn">More &gt;&gt;</div></div>
    </article>
    <article class="card">
      <div class="card-img photo" role="img" aria-label="Float plane on a calm lake"></div>
      <h3>Mallard MX5 -82/89</h3>
      <p>Experimental clipped wing +9 /-6G airshow performer for sale in Norway. Two stroke Bluecrest BT70 fully inverted system.<br>Asking <span class="price">€ 26000</span><br>Name: Arne Solvik, <span class="email">Email</span><br>Phone: +4790001234<br>Date: 2013-10-04 12:23:08</p>
      <div class="card-foot"><div class="btn">More &gt;&gt;</div></div>
    </article>
    <article class="card">
      <div class="card-img photo" role="img" aria-label="Aluminium floats in a workshop"></div>
      <h3>Aluminum Floats from Johan Fellner.</h3>
      <p>Experimental clipped wing +9 /-6G airshow performer for sale in Norway. Two stroke Bluecrest BT70 fully inverted system.<br>Asking <span class="price">€ 26000</span><br>Name: Arne Solvik, <span class="email">Email</span><br>Phone: +4790001234<br>Date: 2013-10-04 12:23:08</p>
      <div class="card-foot"><div class="btn">More &gt;&gt;</div></div>
    </article>
    <article class="card">
      <div class="card-img photo" role="img" aria-label="Aircraft vacuum pump part"></div>
      <h3>Vacuumpump</h3>
      <p>Experimental clipped wing +9 /-6G airshow performer for sale in Norway. Two stroke Bluecrest BT70 fully inverted system.<br>Asking <span class="price">€ 26000</span><br>Name: Arne Solvik, <span class="email">Email</span><br>Phone: +4790001234<br>Date: 2013-10-04 12:23:08</p>
      <div class="card-foot"><div class="btn">More &gt;&gt;</div></div>
    </article>
  </section>

  <div class="abs rule"></div>
  <div class="abs pager" style="left:312px">1</div>
  <div class="abs pager" style="left:330px">2</div>
  <div class="abs pager" style="left:348px">3</div>
  <div class="abs pager" style="left:366px">4</div>
  <div class="abs pager" style="left:405px">10</div>
</main>

<aside>
  <section class="abs panel news">
    <h2 class="panel-head">Latest News</h2>
    <div class="news-item" style="top:38px"><div class="pic photo" role="img" aria-label="Seaplane at a dock"></div><p>Nov 5, 2013<br>Sed ut perspiciatis unde omnis iste natus error sit voluptatem accusantium rem aperiam,<span class="more">More &gt;&gt;</span></p></div>
    <div class="news-item" style="top:95px"><div class="pic photo" role="img" aria-label="Small aircraft on grass strip"></div><p>Nov 5, 2013<br>Sed ut perspiciatis unde omnis iste natus error sit voluptatem accusantium rem aperiam,<span class="more">More &gt;&gt;</span></p></div>
    <div class="news-item" style="top:153px"><div class="pic photo" role="img" aria-label="Cockpit instruments"></div><p>Nov 5, 2013<br>Sed ut perspiciatis unde omnis iste natus error sit voluptatem accusantium rem aperiam,<span class="more">More &gt;&gt;</span></p></div>
  </section>

  <section class="abs panel clips">
    <h2 class="panel-head">Clips</h2>
    <div class="clip" style="top:37px"><div class="pic photo" role="img" aria-label="Aerobatic aircraft in flight"></div><p>Sed ut perspiciatis unde omnis iste natus error sit voluptatem accusantium rem aperiam,<span class="more">More &gt;&gt;</span></p></div>
    <div class="clip" style="top:106px"><div class="pic photo" role="img" aria-label="Red and white aircraft on grass"></div><p>Sed ut perspiciatis unde omnis iste natus error sit voluptatem accusantium rem aperiam,<span class="more">More &gt;&gt;</span></p></div>
  </section>

  <section class="abs ads">
    <div><b>Cheap hotels</b><br>Find Hotels By Price, Star Rating Or Location. Cheap hotels<i>www.StayFinder.com</i></div>
    <div><b>Hotel Seaside Bay</b><br>We Are Right Where You Want To Be Best Value Inn Book It<i>www.seasidebayinn.com</i></div>
    <div><b>Harbor Discount Hotels</b><br>Harbor Inns - Official Site. View Rates, Book Rooms &amp; Get Online Specials.<i>www.harborinns.com</i></div>
    <div><b>Desert Cheap Hotel</b><br>Searching for cheap desert hotels? See our desert cheap hotel guide.<i>DesertStayHotel.net</i></div>
    <span class="ads-tag">Ads by PlaceMint</span>
  </section>

  <div class="abs banner1" role="img" aria-label="Purple conference banner advertisement"></div>
  <div class="abs banner2" role="img" aria-label="Social app banner advertisement with phone screens"></div>
</aside>

<footer>
  <div class="connect">Connect With Us</div>
  <div class="social" aria-label="Social links"><span></span><span></span><span></span><span></span><span></span><span></span></div>
  <div class="legal">Privacy | Disclaimer | Terms<br>© 2013 vingtorget, All Rights Reserved<br>X2</div>
</footer>
</body>
</html>
```